SkyvornQ Business Cards and Stationary Design

Need a design for our business cards and stationary. I want to carry on the theme of the logo. I want the business cards to have a design on the back. I would like the business cards and the stationary to carry the same theme, design scheme, and branding

Target Market(s)

Airlines and Maintenance Facilities

Industry/Entity Type

Aviation

Contact Information for Business Card

Name
Position Title
Address: 4827 Trellis Hollow Road, Fort Pierce, Florida, 34951
Office Number
Mobile Number
Email
Website

Font styles to use
Serif
Sans Serif

Colors

Designer to choose colors to be used in the design.

```html
<!DOCTYPE html>
<html lang="en">
<head>
<meta charset="utf-8">
<title>SkyvornQ Business Cards</title>
<link rel="stylesheet" href="https://fonts.googleapis.com/css2?family=Jost:wght@300;400;600;700&family=Source+Sans+3:wght@400&display=swap">
<style>
  :root {
    --navy: #14284d;
    --navy-deep: #11254a;
    --blue-bright: #2a9ad8;
    --blue-mid: #2169a8;
    --blue-dark: #22407e;
    --white: #ffffff;
    --stage-light: #e6e7e9;
    --stage-dark: #d2d3d5;
  }
  * { box-sizing: border-box; margin: 0; padding: 0; }
  html, body { width: 1200px; height: 1155px; overflow: hidden; }
  body {
    position: relative;
    background: linear-gradient(135deg, var(--stage-light), var(--stage-dark));
    font-family: "Source Sans 3", "Myriad Pro", sans-serif;
  }
  .card {
    position: absolute;
    width: 766px;
    height: 437px;
    overflow: hidden;
  }
  .card--front {
    left: 381px; top: 109px;
    border-radius: 22px;
    background: var(--white);
    border: 1px solid #555;
  }
  .card--back {
    left: 91px; top: 575px;
    border-radius: 42px;
    background: var(--navy);
  }
  .card__art { position: absolute; inset: 0; }
  .brand-ring {
    position: absolute;
    border-radius: 50%;
    border-style: solid;
  }
  .card--front .brand-ring {
    left: 151px; top: 128px; width: 108px; height: 108px;
    border-width: 6px; border-color: var(--blue-mid);
  }
  .card--back .brand-ring {
    left: 312px; top: 115px; width: 142px; height: 142px;
    border-width: 7px; border-color: var(--white);
  }
  .wordmark {
    position: absolute;
    font-family: "Jost", sans-serif;
    font-weight: 700;
    letter-spacing: 0.16em;
    white-space: nowrap;
    transform: translateX(-50%);
  }
  .card--front .wordmark {
    left: 209px; top: 248px;
    font-size: 40px; color: var(--navy);
  }
  .card--back .wordmark {
    left: 388px; top: 272px;
    font-size: 50px; color: var(--white);
  }
  .card__url {
    position: absolute;
    left: 383px; top: 372px;
    transform: translateX(-50%);
    color: var(--white);
    font-size: 24px;
    letter-spacing: 0.22em;
    white-space: nowrap;
  }
  .contact {
    position: absolute;
    right: 36px; top: 78px;
    text-align: right;
    color: var(--white);
  }
  .contact__name {
    font-family: "Jost", sans-serif;
    font-weight: 600;
    font-size: 27px;
    line-height: 32px;
  }
  .contact__title {
    font-family: "Jost", sans-serif;
    font-weight: 300;
    font-size: 24px;
    line-height: 32px;
    margin-bottom: 22px;
  }
  .contact__list { list-style: none; }
  .contact__item {
    display: flex;
    justify-content: flex-end;
    align-items: center;
    gap: 5px;
    font-size: 18px;
    line-height: 27.3px;
  }
  .contact__item--gap { margin-top: 24px; }
  .contact__icon { width: 17px; height: 17px; flex: none; }
  .contact__line { display: block; font-size: 18px; line-height: 27px; }
</style>
</head>
<body>

<section class="card card--front" aria-label="Business card front">
  <svg class="card__art" viewBox="0 0 766 437" aria-hidden="true">
    <defs>
      <radialGradient id="panelGlow" cx="0.58" cy="0.55" r="0.75">
        <stop offset="0" stop-color="var(--blue-bright)"/>
        <stop offset="0.55" stop-color="var(--blue-mid)"/>
        <stop offset="1" stop-color="var(--blue-dark)"/>
      </radialGradient>
    </defs>
    <path d="M404 0 H766 V437 H413 Q480 240 404 0 Z" fill="url(#panelGlow)"/>
    <path d="M363 0 H404 Q480 240 413 437 H374 Q450 230 363 0 Z" fill="var(--navy)"/>
    <path d="M401 96 Q452 250 428 420 Q468 250 401 96 Z" fill="var(--white)" opacity="0.9"/>
  </svg>
  <div class="brand-ring" aria-hidden="true"></div>
  <div class="wordmark">SKYVORNQ</div>

  <div class="contact">
    <div class="contact__name">DANIEL HARWICK</div>
    <div class="contact__title">PRESIDENT</div>
    <ul class="contact__list">
      <li class="contact__item">
        <svg class="contact__icon" viewBox="0 0 20 20" fill="none" stroke="currentColor" stroke-width="1.6"><circle cx="10" cy="10" r="8.5"/><path d="M7 5.5l1.6 2.3-1 1.1q1 2 3 3l1.1-1 2.3 1.6-1 1.6q-4 0-7-4.6z" fill="currentColor" stroke="none"/></svg>
        012-345-6789
      </li>
      <li class="contact__item">
        <svg class="contact__icon" viewBox="0 0 20 20" fill="none" stroke="currentColor" stroke-width="1.6"><circle cx="10" cy="10" r="8.5"/><rect x="7" y="5" width="6" height="10" rx="1"/></svg>
        012-345-6789
      </li>
      <li class="contact__item">
        <svg class="contact__icon" viewBox="0 0 20 20" fill="none" stroke="currentColor" stroke-width="1.6"><circle cx="10" cy="10" r="8.5"/><rect x="5.5" y="7" width="9" height="6.5"/><path d="M5.5 7l4.5 3.5 4.5-3.5"/></svg>
        info@skyvornq.com
      </li>
      <li class="contact__item">
        <svg class="contact__icon" viewBox="0 0 20 20" fill="none" stroke="currentColor" stroke-width="1.4"><circle cx="10" cy="10" r="8.5"/><ellipse cx="10" cy="10" rx="3.8" ry="8.5"/><path d="M1.5 10h17M3 5.5h14M3 14.5h14"/></svg>
        www.skyvornq.com
      </li>
      <li class="contact__item contact__item--gap">
        <svg class="contact__icon" viewBox="0 0 20 20" fill="none" stroke="currentColor" stroke-width="1.6"><circle cx="10" cy="10" r="8.5"/><path d="M10 15s-3.5-3.5-3.5-6a3.5 3.5 0 017 0c0 2.5-3.5 6-3.5 6z"/><circle cx="10" cy="9" r="1.2" fill="currentColor"/></svg>
        123, Street Name, City Name
      </li>
    </ul>
    <span class="contact__line">Zipcode-012345</span>
  </div>
</section>

<section class="card card--back" aria-label="Business card back">
  <div class="brand-ring" aria-hidden="true"></div>
  <div class="wordmark">SKYVORNQ</div>
  <div class="card__url">www.skyvornq.com</div>
</section>

</body>
</html>
```